Biz Card Design TVCP

New business card for a new company.
Logo was completed by a designer on ArtHarbor and looking to continue requesting additional services.
Company Name: Tidal Vector Power Consulting
Although this company is starting in Canada, we will be moving towards a global presence within the next 6 months.
Key elements to this business are as follows.
Energy Procurement
Energy Reduction Services
Demand Side Consulting
Energy Efficiency Consulting
Saving Clients Money
Helping Them Go "Green"
Managing Their Energy Requirements
Basically the goal for our company is to find the best procurement solution for our clients and reduce their energy consumption. This reduces their expenses and the amount of greenhouse gas they produce on a daily basis.
I have been in the energy footprint for the last 20 years and know that most companies are looking to "do whatever is necessary to get them to sign on the dotted line". I would prefer to walk away from a client that I can't help than to put them into a situation that they will regret for years to come. This is where the "TIDAL" part of the company name comes from.
The following is a catch phrase that encompasses what we do.
"Reducing your carbon footprint & energy bill at the same time!"
The back of the card needs to have this statement along with some sort of illustration. The back is a playground for creative ideas.
The front of the card needs the following.
Logo.
First & Last Name (Gus Marwick)
Title (Energy Warrior)
Phone Number (555) 314-2718
Fax Number (555) 271-8314
Email Address gus@tidalvectorpowerconsulting.example
Address 47 fenwick rd Toronto Ontario K4T 2P9
I want it to be a card that is remembered when any of my staff give it to a customer. It HAS to stand out.
Target Market(s)
Business Owners, Decision Makers, 30 to 65+
Industry/Entity Type
Business
Look and feel

```html
<!DOCTYPE html>
<html lang="en">
<head>
<meta charset="utf-8">
<title>TVCP Business Card</title>
<link rel="stylesheet" href="https://fonts.googleapis.com/css2?family=Montserrat:ital,wght@0,400;0,600;0,700;1,400&family=Playfair+Display:ital@1&display=swap">
<style>
  :root {
    --brand-blue: #3d6fc0;
    --brand-blue-text: #3b6cb6;
    --brand-green: #22b24c;
    --brand-green-text: #3cae48;
    --card-border: #b9b9b9;
    --paper: #ffffff;
    --label-ink: #222222;
    --reverse-ink: #ffffff;
  }
  * { margin: 0; padding: 0; box-sizing: border-box; }
  html, body {
    width: 1200px;
    height: 900px;
    overflow: hidden;
    background: var(--paper);
  }
  .canvas {
    position: relative;
    width: 1200px;
    height: 900px;
    font-family: "Montserrat", sans-serif;
  }
  .card {
    position: absolute;
    width: 416px;
    height: 240px;
    overflow: hidden;
  }
  .card-front {
    left: 394px;
    top: 164px;
    border: 1px solid var(--card-border);
    background: var(--paper);
    text-align: center;
  }
  .wordmark {
    position: absolute;
    left: 0; right: 0;
    top: 70px;
    font-weight: 600;
    font-size: 17px;
    letter-spacing: -0.3px;
    color: var(--brand-blue-text);
  }
  .holder-name {
    position: absolute;
    left: 0; right: 0;
    top: 120px;
    font-weight: 700;
    font-size: 14px;
    letter-spacing: 1px;
    color: var(--brand-blue-text);
  }
  .contact {
    position: absolute;
    left: 0; right: 0;
    top: 160px;
    font-size: 12.5px;
    line-height: 19px;
  }
  .contact .address, .contact .email { color: var(--brand-blue-text); }
  .contact .numbers { color: var(--brand-green-text); }
  .contact .sep { margin: 0 8px; }

  .side-label {
    position: absolute;
    font-family: "Playfair Display", serif;
    font-style: italic;
    font-size: 13px;
    letter-spacing: 1.5px;
    color: var(--label-ink);
  }
  .label-front { left: 398px; top: 414px; }
  .label-back-blue { left: 104px; top: 784px; }
  .label-back-green { left: 716px; top: 784px; }

  .or-divider {
    position: absolute;
    left: 596px;
    top: 640px;
    font-style: italic;
    font-size: 17px;
    color: var(--label-ink);
  }

  .card-back { top: 536px; }
  .card-back-blue { left: 96px; background: var(--brand-blue); }
  .card-back-green { left: 708px; background: var(--brand-green); }
  .globe-art {
    position: absolute;
    left: 0; top: 0;
    width: 416px; height: 240px;
  }
  .tagline {
    position: absolute;
    right: 30px;
    top: 96px;
    text-align: right;
    font-style: italic;
    font-size: 15.5px;
    line-height: 24px;
    color: var(--reverse-ink);
  }
  .tagline .accent { color: var(--brand-blue); }
  .card-back-green .tagline { text-align: left; left: 104px; right: auto; }
  .back-mark {
    position: absolute;
    right: 16px;
    bottom: 12px;
    font-weight: 600;
    font-size: 11px;
    letter-spacing: 0.5px;
    color: var(--reverse-ink);
  }
</style>
</head>
<body>
<main class="canvas">
  <section class="card card-front">
    <div class="wordmark">Tidal Vector Power Consulting</div>
    <div class="holder-name">GUS MARWICK</div>
    <div class="contact">
      <div class="address">47 fenwick rd Toronto Canada K4T 2P9</div>
      <div class="numbers">P (555) 314-2718<span class="sep">•</span>F (555) 271-8314</div>
      <div class="email">gus@tidalvectorpowerconsulting.example</div>
    </div>
  </section>
  <div class="side-label label-front">front</div>

  <section class="card card-back card-back-blue">
    <svg class="globe-art" role="img" aria-label="Faint globe illustration" viewBox="0 0 416 240">
      <defs>
        <radialGradient id="globeBlue" cx="0.5" cy="0.5" r="0.5">
          <stop offset="0" stop-color="#ffffff" stop-opacity="0.14"/>
          <stop offset="1" stop-color="#ffffff" stop-opacity="0.08"/>
        </radialGradient>
      </defs>
      <circle cx="120" cy="112" r="170" fill="url(#globeBlue)"/>
    </svg>
    <p class="tagline">Reducing your carbon footprint<br>&amp; energy bill at the same time!</p>
    <div class="back-mark">TVCP</div>
  </section>
  <div class="side-label label-back-blue">back</div>

  <div class="or-divider">or</div>

  <section class="card card-back card-back-green">
    <svg class="globe-art" role="img" aria-label="Faint globe illustration" viewBox="0 0 416 240">
      <defs>
        <radialGradient id="globeGreen" cx="0.5" cy="0.5" r="0.5">
          <stop offset="0" stop-color="#ffffff" stop-opacity="0.14"/>
          <stop offset="1" stop-color="#ffffff" stop-opacity="0.08"/>
        </radialGradient>
      </defs>
      <circle cx="120" cy="112" r="170" fill="url(#globeGreen)"/>
    </svg>
    <p class="tagline">Reducing <span class="accent">your carbon footprint</span><br><span class="accent">&amp; energy bill at the same time!</span></p>
    <div class="back-mark">TVCP</div>
  </section>
  <div class="side-label label-back-green">back</div>
</main>
</body>
</html>
```